Stationery for a private security company, "Brenmoor Security Services Ltd."

Needed is a stationery design for a private security company. The designs must show professionalism and that our company mean nothing but business. Watermark of the company logo on the letterhead page is also a must. The final design must represent innovation and professionalism. It would be great if designers could integrate the colours black and silver onto the cards and letterheads..

Thank you

```html
<!DOCTYPE html>
<html lang="en">
<head>
<meta charset="utf-8">
<title>Brenmoor Security Services Ltd. – Stationery</title>
<link href="https://fonts.googleapis.com/css2?family=Bitter:wght@400;700&family=Open+Sans:wght@300;400&display=swap" rel="stylesheet">
<style>
  :root {
    --ink: #0d0d0d;
    --paper: #ffffff;
    --silver: #a9b4ba;
    --silver-light: #d4dadd;
    --flap-grey: #b3bec4;
    --stage: #3b2a1e;
    --label: #f1e6dc;
    --rule: #333333;
  }
  * { box-sizing: border-box; margin: 0; padding: 0; }
  html, body { width: 1200px; height: 515px; overflow: hidden; }
  body {
    background: var(--stage);
    font-family: 'Bitter', Georgia, serif;
    color: var(--ink);
    position: relative;
  }
  .piece { position: absolute; background: var(--paper); overflow: hidden; }
  .piece svg.fill { position: absolute; left: 0; top: 0; width: 100%; height: 100%; }
  .brand {
    position: absolute;
    font-family: 'Bitter', Georgia, serif;
    font-weight: 700;
    color: var(--ink);
    text-transform: uppercase;
    line-height: 1.05;
    display: flex; align-items: center; gap: 4px;
  }
  .brand .name { display: block; }
  .brand .name span { display: block; }
  .brand .name .main { font-size: 1em; letter-spacing: .06em; }
  .brand .name .sub { font-size: .42em; letter-spacing: .02em; }

  .contact { position: absolute; font-size: 6.4px; line-height: 1.4; text-align: right; white-space: nowrap; }
  .contact li { list-style: none; }
  .contact b { font-weight: 400; display: inline-block; width: 6px; height: 5px; background: var(--ink); margin-right: 3px; vertical-align: middle; }
  .contact b.round { border-radius: 50%; width: 5px; }

  .foot-line { position: absolute; left: 5px; bottom: 3px; font-size: 6.2px; display: flex; gap: 6px; align-items: center; white-space: nowrap; }
  .foot-line svg { width: 6px; height: 7px; vertical-align: -1px; margin-right: 2px; }
  .tagline { position: absolute; right: 5px; bottom: 4px; font-size: 5.4px; font-weight: 700; color: var(--paper); white-space: nowrap; }

  .option-label { position: absolute; top: 474px; font-family: 'Open Sans', Arial, sans-serif; font-size: 15px; color: var(--label); transform: translateX(-50%); }

  .fax-title { position: absolute; left: 14px; top: 112px; font-family: 'Open Sans', Arial, sans-serif; font-weight: 300; font-size: 20px; }
  .fax-row { position: absolute; height: 12px; border-bottom: 1px solid var(--rule); font-family: 'Open Sans', Arial, sans-serif; font-size: 5.6px; }
  .fax-checks { position: absolute; left: 14px; top: 234px; width: 308px; display: flex; justify-content: space-between; font-family: 'Open Sans', Arial, sans-serif; font-size: 5.8px; }
  .fax-checks span::before { content: ""; display: inline-block; width: 6px; height: 6px; border: 1px solid var(--rule); margin-right: 4px; vertical-align: -1px; }

  .env-address { position: absolute; left: 11px; top: 68px; font-size: 6.6px; }
  .env-web { position: absolute; left: 11px; bottom: 3px; font-size: 6.6px; color: var(--paper); }

  .card-text { position: absolute; font-size: 4.2px; line-height: 1.4; white-space: nowrap; }
  .card-name { position: absolute; font-size: 6px; line-height: 1.1; }
  .card-name small { display: block; font-size: 4px; }
  .card-dark { background: var(--ink); }
  .card-dark .brand { color: var(--paper); }
  .card-dark .web { position: absolute; width: 100%; top: 63px; color: var(--silver); font-size: 4.6px; letter-spacing: .05em; }
</style>
</head>
<body>

<svg width="0" height="0" style="position:absolute" aria-hidden="true">
  <defs>
    <linearGradient id="silver-grad" x1="0" x2="1">
      <stop offset="0" stop-color="#ffffff"/>
      <stop offset=".55" stop-color="#8e989d"/>
      <stop offset="1" stop-color="#3a3a3a"/>
    </linearGradient>
    <symbol id="header-swoosh" viewBox="0 0 336 100" preserveAspectRatio="none">
      <path d="M0,0 H336 V92 C332,56 316,34 262,28 C190,22 112,26 42,13 C22,9 8,7 0,7 Z" fill="#0d0d0d"/>
      <path d="M66,22 C146,32 226,22 290,28 C318,33 329,50 333,76" fill="none" stroke="url(#silver-grad)" stroke-width="3"/>
    </symbol>
    <symbol id="footer-band" viewBox="0 0 336 40" preserveAspectRatio="none">
      <path d="M208,40 L238,10 H336 V40 Z" fill="#0d0d0d"/>
      <path d="M233,40 L243,28 H336 V40 Z" fill="#a9b4ba"/>
      <circle cx="300" cy="18" r="5" fill="#3a3a3a"/>
    </symbol>
  </defs>
</svg>

<!-- Letterhead -->
<section class="piece letterhead" style="left:24px;top:34px;width:336px;height:434px;">
  <svg style="position:absolute;left:0;top:0;width:336px;height:100px"><use href="#header-swoosh" width="336" height="100"/></svg>
  <div class="brand" style="left:8px;top:44px;font-size:12px;"><span class="name"><span class="main">Brenmoor</span><span class="sub" style="font-size:5.4px">Security Services Ltd.</span></span></div>
  <ul class="contact" style="right:36px;top:46px;">
    <li>✆ 123-456-7856</li>
    <li><b></b>brenmoorsecurity@mailbox.com</li>
    <li><b class="round"></b>www.brenmoorsecurity.com</li>
  </ul>
  <svg style="position:absolute;left:0;bottom:0;width:336px;height:40px"><use href="#footer-band" width="336" height="40"/></svg>
  <div class="foot-line">
    <span>✆ 123-456-7890</span>
    <span><svg viewBox="0 0 6 8"><path d="M3,0 A3,3 0 0 1 6,3 C6,5 3,8 3,8 C3,8 0,5 0,3 A3,3 0 0 1 3,0 Z" fill="#0d0d0d"/></svg>Street Name, City Name, State Zipcode</span>
  </div>
  <div class="tagline">Providing World Class Security</div>
</section>
<div class="option-label" style="left:192px;">Option-1</div>

<!-- Fax sheet -->
<section class="piece fax" style="left:376px;top:34px;width:336px;height:434px;">
  <svg style="position:absolute;left:0;top:0;width:336px;height:100px"><use href="#header-swoosh" width="336" height="100"/></svg>
  <div class="brand" style="left:8px;top:44px;font-size:12px;"><span class="name"><span class="main">Brenmoor</span><span class="sub" style="font-size:5.4px">Security Services Ltd.</span></span></div>
  <ul class="contact" style="right:36px;top:46px;">
    <li>✆ 123-456-7856</li>
    <li><b></b>brenmoorsecurity@mailbox.com</li>
    <li><b class="round"></b>www.brenmoorsecurity.com</li>
  </ul>
  <div class="fax-title">FAX</div>
  <div class="fax-row" style="left:14px;top:146px;width:170px">To :</div>
  <div class="fax-row" style="left:189px;top:146px;width:131px">From :</div>
  <div class="fax-row" style="left:14px;top:164px;width:170px">Fax :</div>
  <div class="fax-row" style="left:189px;top:164px;width:131px">Pages :</div>
  <div class="fax-row" style="left:14px;top:182px;width:170px">Phone :</div>
  <div class="fax-row" style="left:189px;top:182px;width:131px">Date :</div>
  <div class="fax-row" style="left:14px;top:200px;width:170px">Re :</div>
  <div class="fax-row" style="left:189px;top:200px;width:131px">CC :</div>
  <div class="fax-checks">
    <span>Urgent</span><span>For Review</span><span>Please Comment</span><span>Please Reply</span><span>Please Recycle</span>
  </div>
  <svg style="position:absolute;left:0;bottom:0;width:336px;height:40px"><use href="#footer-band" width="336" height="40"/></svg>
  <div class="foot-line">
    <span>✆ 123-456-7890</span>
    <span><svg viewBox="0 0 6 8"><path d="M3,0 A3,3 0 0 1 6,3 C6,5 3,8 3,8 C3,8 0,5 0,3 A3,3 0 0 1 3,0 Z" fill="#0d0d0d"/></svg>Street Name, City Name, State Zipcode</span>
  </div>
  <div class="tagline">Providing World Class Security</div>
</section>
<div class="option-label" style="left:550px;">Option-2</div>

<!-- Envelope back, silver flap -->
<section class="piece envelope-back" style="left:776px;top:35px;width:374px;height:168px;box-shadow:0 0 3px rgba(0,0,0,.3)">
  <svg class="fill" viewBox="0 0 374 168" preserveAspectRatio="none">
    <path d="M0,0 H374 V22 L206,84 C196,88 178,88 168,84 L0,22 Z" fill="var(--flap-grey)"/>
    <circle cx="187" cy="40" r="12" fill="#c6cfd3"/>
  </svg>
</section>

<!-- Envelope back, black flap -->
<section class="piece envelope-back" style="left:764px;top:109px;width:374px;height:132px;box-shadow:0 0 3px rgba(0,0,0,.3)">
  <svg class="fill" viewBox="0 0 374 132" preserveAspectRatio="none">
    <path d="M0,0 H374 V8 C374,20 368,28 356,32 L214,62 C196,66 178,66 160,62 L18,32 C6,28 0,20 0,8 Z" fill="var(--ink)"/>
    <circle cx="187" cy="36" r="11" fill="#2c2c2c"/>
  </svg>
</section>

<!-- Envelope front -->
<section class="piece envelope" style="left:738px;top:192px;width:376px;height:168px;box-shadow:0 0 4px rgba(0,0,0,.35)">
  <svg style="position:absolute;left:0;top:0;width:376px;height:60px"><use href="#header-swoosh" width="376" height="60"/></svg>
  <div class="brand" style="left:11px;top:46px;font-size:11px;"><span class="name"><span class="main">Brenmoor</span><span class="sub" style="font-size:5px">Security Services Ltd.</span></span></div>
  <div class="env-address">Street Name, City Name, State Zipcode</div>
  <svg class="fill" viewBox="0 0 376 168" preserveAspectRatio="none">
    <path d="M0,154 H200 L232,134 H376 V168 H0 Z" fill="var(--ink)"/>
    <path d="M232,168 L250,148 H376 V168 Z" fill="var(--silver)"/>
    <circle cx="340" cy="140" r="5" fill="#3a3a3a"/>
  </svg>
  <div class="env-web">www.brenmoorsecurity.com</div>
  <div class="tagline" style="bottom:5px">Providing World Class Security</div>
</section>

<!-- Business card, front variant -->
<section class="piece card" style="left:726px;top:389px;width:139px;height:80px;">
  <svg style="position:absolute;left:0;top:0;width:139px;height:24px"><use href="#header-swoosh" width="139" height="24"/></svg>
  <div class="brand" style="left:4px;top:13px;font-size:5px;"><span class="name"><span class="main">Brenmoor</span><span class="sub" style="font-size:2.6px">Security Services Ltd.</span></span></div>
  <div class="card-name" style="right:10px;top:13px;text-align:right">Your Name<small>Title</small></div>
  <div class="card-text" style="left:5px;top:38px">✆ 123-456-7890<br>✆ 123-456-7856<br>brenmoorsecurity@mailbox.com<br>www.brenmoorsecurity.com</div>
  <div class="card-text" style="left:5px;top:62px">Street Name, City Name, State Zipcode</div>
  <svg style="position:absolute;left:0;bottom:0;width:139px;height:14px"><use href="#footer-band" width="139" height="14"/></svg>
</section>

<!-- Business card, logo left variant -->
<section class="piece card" style="left:874px;top:389px;width:139px;height:80px;">
  <div class="brand" style="left:6px;top:30px;font-size:6.4px;"><span class="name"><span class="main">Brenmoor</span><span class="sub" style="font-size:3px">Security Services Ltd.</span></span></div>
  <div style="position:absolute;left:65px;top:14px;width:1px;height:44px;background:var(--rule)"></div>
  <div class="card-name" style="left:70px;top:14px">Your Name<small>Title</small></div>
  <div class="card-text" style="left:70px;top:30px">✆ 123-456-7890<br>✆ 123-456-7856<br>brenmoorsecurity@mailbox.com<br>www.brenmoorsecurity.com</div>
  <div class="card-text" style="left:4px;top:68px">Street Name, City Name, State Zipcode</div>
  <svg style="position:absolute;left:0;bottom:0;width:139px;height:14px"><use href="#footer-band" width="139" height="14"/></svg>
</section>

<!-- Business card, dark back -->
<section class="piece card card-dark" style="left:1027px;top:390px;width:139px;height:80px;">
  <svg class="fill" viewBox="0 0 139 80"><circle cx="87" cy="24" r="10" fill="#2a2a2a"/></svg>
  <div class="brand" style="left:0;width:100%;justify-content:flex-end;padding-right:14px;top:40px;font-size:7.6px;text-align:center"><span class="name"><span class="main">Brenmoor</span><span class="sub" style="font-size:3.4px">Security Services Ltd.</span></span></div>
  <div class="web" style="text-align:right;padding-right:12px">www.brenmoorsecurity.com</div>
</section>

</body>
</html>
```